Unique Business Card Design

Unique Business Card design for our orthotic and prosthetic company. Our logo is on our website, color is light blue. Unique shape (artificial leg shaped, vertical, etc..) preferred. Logo, business name, individual name and basic demographics needed.

Industry/Entity Type

Business

Contact Information for Business Card

Logo, Industry, Phone # Logo, "Prosthetic & Orthotic Services" Place to add individual name and contact info

Colors
cee9f5

Requirements
Must have
• The icon must be there, placement of "Prosthetic & Orthotic Services" can be moved
Nice to have
• Like the mix of light blue, and a little darker blue. One design included the icons from my website which was a nice touch

```html
<!DOCTYPE html>
<html lang="en">
<head>
<meta charset="utf-8">
<title>LimbWorks Inc. — Business Card</title>
<link href="https://fonts.googleapis.com/css2?family=Open+Sans:wght@400;700&family=Lora:ital@1&display=swap" rel="stylesheet">
<style>
  :root {
    --brand-blue: #2a6dc4;
    --brand-blue-dark: #1f5aa8;
    --paper: #ffffff;
    --rule-grey: #c9ccd1;
    --stage: #3a3a3a;
    --ink-light: #ffffff;
  }
  * { box-sizing: border-box; margin: 0; padding: 0; }
  html, body { width: 1200px; height: 950px; overflow: hidden; }
  body {
    background: var(--stage);
    font-family: "Open Sans", Arial, sans-serif;
    display: flex;
    flex-direction: column;
    align-items: center;
    justify-content: center;
    gap: 60px;
  }
  .card {
    position: relative;
    width: 640px;
    height: 366px;
    border-radius: 22px;
    overflow: hidden;
  }
  /* Front */
  .card--front { background: var(--brand-blue); }
  .lockup {
    position: absolute;
    display: flex;
    align-items: center;
    gap: 24px;
  }
  .card--front .lockup { left: 70px; top: 118px; }
  .lockup__dot {
    width: 118px; height: 118px;
    border-radius: 50%;
    background: var(--paper);
    flex: none;
  }
  .lockup__name {
    font-weight: 700;
    font-size: 40px;
    line-height: 1;
    letter-spacing: -0.5px;
    padding-bottom: 8px;
    border-bottom: 3px solid currentColor;
  }
  .lockup__tagline {
    font-family: "Lora", Georgia, serif;
    font-style: italic;
    font-size: 20px;
    margin-top: 6px;
  }
  .card--front .lockup__name,
  .card--front .lockup__tagline { color: var(--ink-light); }

  /* Back */
  .card--back { background: var(--paper); }
  .card--back .wave { position: absolute; inset: 0; width: 100%; height: 100%; }
  .card--back .lockup { left: 58px; top: 66px; gap: 20px; }
  .card--back .lockup__dot { width: 96px; height: 96px; background: var(--brand-blue); }
  .card--back .lockup__name { color: var(--brand-blue); font-size: 36px; }
  .card--back .lockup__tagline { color: var(--brand-blue); font-size: 18px; }
  .contact {
    position: absolute;
    left: 0; right: 0; top: 206px;
    text-align: center;
    color: var(--ink-light);
    font-size: 14.5px;
    line-height: 1.55;
  }
  .contact__person { font-size: 22px; font-weight: 700; margin-bottom: 4px; }
  .contact__creds { font-size: 14px; }
  .contact__web { letter-spacing: 4px; font-weight: 700; margin-top: 2px; }
</style>
</head>
<body>

  <section class="card card--front" aria-label="Card front">
    <div class="lockup">
      <span class="lockup__dot"></span>
      <div>
        <div class="lockup__name">LIMBWORKS INC.</div>
        <div class="lockup__tagline">Prosthetic &amp; Orthotic Services</div>
      </div>
    </div>
  </section>

  <section class="card card--back" aria-label="Card back">
    <svg class="wave" viewBox="0 0 640 366" preserveAspectRatio="none" aria-hidden="true">
      <path d="M0 300 C 160 200, 420 150, 640 150 L640 160 C 420 162, 160 214, 0 316 Z" fill="var(--rule-grey)"/>
      <path d="M0 312 C 160 210, 420 160, 640 158 L640 366 L0 366 Z" fill="var(--brand-blue)"/>
    </svg>
    <div class="lockup">
      <span class="lockup__dot"></span>
      <div>
        <div class="lockup__name">LIMBWORKS INC.</div>
        <div class="lockup__tagline">Prosthetic &amp; Orthotic Services</div>
      </div>
    </div>
    <div class="contact">
      <div class="contact__person">Mara Kessler, <span class="contact__creds">CO LPO</span></div>
      <div>2250 Harbor Ave., Linden, NY 11590 | P: 555.210.4400</div>
      <div>M: 555.210.4418 &nbsp;F: 555.210.4490 &nbsp;E: mkessler@limbworksinc.com</div>
      <div class="contact__web">www.limbworksinc.com</div>
    </div>
  </section>

</body>
</html>
```